Business cards and stationary design

We just completed the design of our new logo and we need to print new business cards and letterhead for our nonprofit. We are looking for a fresh new design that shows off our new logo. On letterhead, we must have a column on the right or left to include our Board of Directors (up to 45 names) (see attachment)

Industry/Entity Type

Non-Profit

Contact Information for Business Card

Standard business card with name, title, Company name, mailing address phone numbers, email address and website. Tagline on back "Bringing the homeless home"

Font styles to use
Sans Serif

Requirements
Must have
• include pertinent information above
• new logo
• fonts compatible with logo
• should use logo colors only
Nice to have
• tag lines

```html
<!DOCTYPE html>
<html lang="en">
<head>
<meta charset="utf-8">
<title>Hearthway Center – Business Card</title>
<link rel="stylesheet" href="https://fonts.googleapis.com/css2?family=Orbitron:wght@500;700&family=Exo+2:wght@500;600&display=swap">
<style>
  :root {
    --teal: #0f7390;
    --red: #e30613;
    --gold: #e8a300;
    --paper: #ffffff;
    --ink: #2a2a2a;
    --backdrop: #eceae6;
  }
  * { margin: 0; padding: 0; box-sizing: border-box; }
  html, body { width: 1200px; height: 800px; overflow: hidden; }
  body {
    background: var(--backdrop);
    font-family: "Exo 2", sans-serif;
    position: relative;
  }
  .card {
    position: absolute;
    top: 257px;
    width: 500px;
    height: 286px;
    background: var(--paper);
    overflow: hidden;
    box-shadow: 0 6px 18px rgba(0,0,0,.18);
  }
  .card--back { left: 70px; }
  .card--front { left: 630px; }
  .card__shapes { position: absolute; inset: 0; }

  .wordmark { position: absolute; display: flex; align-items: center; gap: 10px; }
  .wordmark__dot { width: 22px; height: 22px; border-radius: 50%; background: var(--gold); flex: none; }
  .wordmark__text {
    font-family: "Exo 2", sans-serif; font-weight: 600; color: var(--ink);
    letter-spacing: .02em; line-height: 1; white-space: nowrap;
  }

  .card--back .wordmark { left: 290px; top: 150px; }
  .card--back .wordmark__text { font-size: 20px; }
  .website {
    position: absolute; right: 24px; top: 22px;
    font-family: "Orbitron", sans-serif; font-weight: 500; font-size: 11px;
    letter-spacing: .1em; color: var(--teal);
  }

  .card--front .wordmark { left: 30px; top: 30px; }
  .card--front .wordmark__text { font-size: 18px; }

  .person { position: absolute; left: 30px; top: 96px; padding-left: 14px; border-left: 4px solid var(--teal); }
  .person__name { font-family: "Orbitron", sans-serif; font-weight: 700; font-size: 15px; color: var(--red); letter-spacing: .04em; }
  .person__title { font-family: "Orbitron", sans-serif; font-weight: 500; font-size: 11px; color: var(--ink); letter-spacing: .06em; margin-top: 3px; }

  .contact { position: absolute; left: 30px; top: 176px; list-style: none; }
  .contact__item { display: flex; align-items: center; gap: 10px; font-size: 13px; color: var(--ink); letter-spacing: .05em; margin-bottom: 10px; }
  .contact__icon { width: 20px; height: 20px; flex: none; }

  .address {
    position: absolute; right: 32px; bottom: 20px; text-align: right;
    font-family: "Orbitron", sans-serif; font-weight: 500; font-size: 11px;
    color: var(--paper); letter-spacing: .06em; line-height: 1.35;
  }
</style>
</head>
<body>

<section class="card card--back" aria-label="Card back">
  <svg class="card__shapes" viewBox="0 0 500 286" aria-hidden="true">
    <polygon points="0,0 200,0 300,286 0,286" fill="var(--red)"/>
    <polygon points="0,120 300,286 0,286" fill="var(--teal)"/>
  </svg>
  <p class="website">WWW.HEARTHWAYDALLAS.ORG</p>
  <div class="wordmark">
    <span class="wordmark__dot"></span>
    <span class="wordmark__text">Hearthway Center</span>
  </div>
</section>

<section class="card card--front" aria-label="Card front">
  <svg class="card__shapes" viewBox="0 0 500 286" aria-hidden="true">
    <polygon points="250,286 420,110 500,286" fill="var(--red)"/>
    <polygon points="365,0 500,0 500,286" fill="var(--gold)"/>
  </svg>
  <div class="wordmark">
    <span class="wordmark__dot"></span>
    <span class="wordmark__text">Hearthway Center</span>
  </div>

  <div class="person">
    <p class="person__name">SAM CARTER</p>
    <p class="person__title">DIRECTOR</p>
  </div>

  <ul class="contact">
    <li class="contact__item">
      <svg class="contact__icon" viewBox="0 0 20 20" aria-hidden="true">
        <circle cx="10" cy="10" r="10" fill="var(--red)"/>
        <path d="M7 5.5c.5-.4 1.1-.3 1.4.2l.8 1.4c.2.4.1.9-.2 1.2l-.6.5c.5 1.1 1.3 1.9 2.4 2.4l.5-.6c.3-.3.8-.4 1.2-.2l1.4.8c.5.3.6.9.2 1.4l-.6.7c-.5.5-1.3.7-2 .4C9.4 12.7 7.3 10.6 6.5 8.3c-.3-.7-.1-1.5.4-2z" fill="#fff"/>
      </svg>
      214.555.0187
    </li>
    <li class="contact__item">
      <svg class="contact__icon" viewBox="0 0 20 20" aria-hidden="true">
        <circle cx="10" cy="10" r="10" fill="var(--red)"/>
        <rect x="5" y="6.5" width="10" height="7" rx="1" fill="#fff"/>
        <path d="M5.3 7l4.7 3.6L14.7 7" fill="none" stroke="var(--red)" stroke-width="1"/>
      </svg>
      EMAIL@hearthwaydallas.org
    </li>
  </ul>

  <p class="address">P.O. BOX 20485<br>DALLAS, TEXAS 75201</p>
</section>

</body>
</html>
```